I need a logo design for a new company based in Tucson called "Mindtrail Lee Corwin". I am a psychotherapist that specializes in clinical psychology with athletes and performers. The final design should incorporate the psychology symbol as a watermark. The logo should convey movement and fluidity. "Mindtrail" is a bit of a play on words combining psychology (head) with sports (coach). Other design interests include mid-century, Harold Ames Whitby. I will want to use the logo for business cards, letterhead and marketing brochures. I will put together a website at a later date. I am attaching a file with some pertinent information for the business card. Thank you.
Lee Corwin
mindtrailleecorwin@quillpost.net

Thank you all for the submissions so far.  I have submitted an additional file with a draft of a new design idea.  Since "mindtrail" is a bit of a play on words, I would like to see something with the two "H's" look something like quotation marks.  If the psychology logo is to be included at all, it needs to be less prominent.     Thank you all.  Lee                               

Target Market(s)

1) Adolescent and adult athletes and performers who are looking to increase their level of performance (Sport and Performance Psychology)
2) Adult psychotherapy patients (Clinical psychology)

Industry/Entity Type

Marketing

Colors

Designer to choose colors to be used in the design.

Requirements
Must have
• 1) Since "mindtrail" is a bit of a play on words, The "H's" need to be in a font that looks somewhat like quotation marks.

Nice to have
• Logo on one side. All other info on the backside?

```html
<!DOCTYPE html>
<html lang="en">
<head>
<meta charset="utf-8">
<title>Mindtrail Lee Corwin – Business Card</title>
<link rel="stylesheet" href="https://fonts.googleapis.com/css2?family=Questrial&display=swap">
<style>
  :root {
    --backdrop: #e9e6e1;
    --navy: #0d3a66;
    --ocean: #1f5d96;
    --sky: #5b91c8;
    --brand-blue: #2a4fa0;
    --accent-orange: #e8731e;
    --text-blue: #2c3f9c;
    --card-white: #ffffff;
    --shadow: rgba(0, 0, 0, 0.22);
  }
  * { margin: 0; padding: 0; box-sizing: border-box; }
  html, body {
    width: 1200px;
    height: 784px;
    overflow: hidden;
    background: var(--backdrop);
    font-family: "Questrial", "Century Gothic", sans-serif;
  }
  .canvas {
    position: relative;
    width: 1200px;
    height: 784px;
  }
  .card {
    position: absolute;
    width: 540px;
    height: 309px;
    border-radius: 4px;
    box-shadow: 0 10px 26px var(--shadow);
    overflow: hidden;
  }
  /* Front side */
  .card-front {
    left: 70px;
    top: 90px;
    background: var(--ocean);
  }
  .front-pattern {
    position: absolute;
    inset: 0;
    background:
      radial-gradient(ellipse 70% 90% at 30% 20%, rgba(140, 185, 230, 0.55), transparent 70%),
      linear-gradient(120deg, var(--sky) 0%, var(--ocean) 45%, var(--navy) 100%);
  }
  .front-brand {
    position: absolute;
    left: 70px;
    top: 92px;
    color: var(--card-white);
  }
  .front-brand .brand-name {
    font-size: 62px;
    letter-spacing: 1px;
    text-transform: uppercase;
    line-height: 1;
  }
  .front-brand .brand-person {
    margin-top: 8px;
    font-size: 24px;
    letter-spacing: 18px;
    padding-left: 6px;
  }
  /* Back side */
  .card-back {
    left: 590px;
    top: 390px;
    background: var(--card-white);
  }
  .back-brand {
    position: absolute;
    left: 46px;
    top: 44px;
  }
  .back-brand .brand-name {
    color: var(--brand-blue);
    font-size: 50px;
    letter-spacing: 1px;
    text-transform: uppercase;
    line-height: 1;
  }
  .back-brand .brand-person {
    margin-top: 6px;
    color: var(--accent-orange);
    font-size: 20px;
    letter-spacing: 15px;
    padding-left: 4px;
  }
  .contact {
    position: absolute;
    left: 46px;
    top: 176px;
  }
  .contact-name {
    color: var(--accent-orange);
    font-size: 19px;
    font-weight: 700;
  }
  .contact-role {
    color: var(--text-blue);
    font-size: 11px;
    margin: 3px 0 8px 4px;
  }
  .contact-list {
    list-style: none;
  }
  .contact-list li {
    display: flex;
    align-items: center;
    gap: 8px;
    color: var(--text-blue);
    font-size: 15px;
    line-height: 20px;
  }
  .contact-list svg {
    width: 15px;
    height: 15px;
    flex: none;
    fill: var(--accent-orange);
  }
</style>
</head>
<body>
<main class="canvas">

  <section class="card card-front" aria-label="Card front">
    <div class="front-pattern" role="img" aria-label="Blue background with a field of pale oval dots receding in perspective"></div>
    <div class="front-brand">
      <div class="brand-name">Mindtrail</div>
      <div class="brand-person">Lee Corwin</div>
    </div>
  </section>

  <section class="card card-back" aria-label="Card back">
    <div class="back-brand">
      <div class="brand-name">Mindtrail</div>
      <div class="brand-person">Lee Corwin</div>
    </div>
    <div class="contact">
      <div class="contact-name">Lee Corwin</div>
      <div class="contact-role">Psychologist</div>
      <ul class="contact-list">
        <li>
          <svg viewBox="0 0 16 16" aria-hidden="true"><path d="M3.5 1.5l2.5 3-1.5 1.8c.9 1.9 2.3 3.3 4.2 4.2L10.5 9l3 2.5-1.4 2.6C6.8 14 2 9.2 1.9 3z"/></svg>
          1520 555 0187
        </li>
        <li>
          <svg viewBox="0 0 16 16" aria-hidden="true"><path d="M8 1.5L1 8h2v6.5h4v-4h2v4h4V8h2z"/></svg>
          PO Box 40517 AZ 85719
        </li>
        <li>
          <svg viewBox="0 0 16 16" aria-hidden="true"><path d="M1 3.5h14v9H1z M1.8 4.2L8 9l6.2-4.8" stroke="#fff" stroke-width="1.2"/></svg>
          mindtrailleecorwin@quillpost.net
        </li>
        <li>
          <svg viewBox="0 0 16 16" aria-hidden="true"><circle cx="8" cy="8" r="7"/><path d="M1 8h14M8 1c-3 3.5-3 10.5 0 14M8 1c3 3.5 3 10.5 0 14" stroke="#fff" stroke-width="1" fill="none"/></svg>
          www.mindtrailleecorwin.com
        </li>
      </ul>
    </div>
  </section>

</main>
</body>
</html>
```